Business Card Design Project

The business card is for an educational company that provides personalised tuition to students.

The company logo is in orange and blue (as provided) and should be included in the name card design

The philosophy of the company is to make learning a comfortable experience for student as such design of the namecard should look fresh and has a bit of the 'wow' factor. Some of the namecard design that appeals to me are as uploaded under Sample Design.

The particulars that need to be provided are:
(1): Company Name (Lantern Education)
(1): Name
(2): Educational qualifications which will appear below name
(3): Mobile number
(4): Email address
(5): Website

Industry/Entity Type

Business

Requirements
Must have
• (1): Company Logo

(2): The card background should preferably be coloured both for the front side and back.

(3): The choice of font is important as part of the selection consideration. There is no preferred font that I have selected, designer is free to choose the font that will complement their design.

```html
<!DOCTYPE html>
<html lang="en">
<head>
<meta charset="utf-8">
<title>Lantern Education Business Cards</title>
<link rel="stylesheet" href="https://fonts.googleapis.com/css2?family=Crimson+Pro:wght@500&family=Titillium+Web:wght@300;400;700&display=swap">
<style>
  :root {
    --page-bg: #e4e5e6;
    --card-deep: #0f2f3e;
    --card-mid: #1b4a58;
    --card-edge: #0b2430;
    --ink-white: #ffffff;
    --ink-soft: #c9d8dd;
  }
  * { margin: 0; padding: 0; box-sizing: border-box; }
  html, body {
    width: 1200px;
    height: 861px;
    overflow: hidden;
    background: var(--page-bg);
  }
  .stage {
    position: relative;
    width: 1200px;
    height: 861px;
  }
  .card {
    position: absolute;
    top: 285px;
    width: 500px;
    height: 290px;
    overflow: hidden;
    box-shadow: 0 10px 26px rgba(0,0,0,0.25);
  }
  .card--front { left: 70px; }
  .card--back { left: 630px; }
  .card__pattern {
    position: absolute;
    inset: 0;
    background: radial-gradient(ellipse at 50% 45%, var(--card-mid) 0%, var(--card-deep) 65%, var(--card-edge) 100%);
  }
  .card__content {
    position: relative;
    height: 100%;
    display: flex;
    flex-direction: column;
    align-items: center;
    color: var(--ink-white);
    font-family: "Titillium Web", sans-serif;
  }
  .brand {
    display: flex;
    align-items: center;
  }
  .brand__square {
    background: var(--ink-white);
    border-radius: 8px;
  }
  .brand__name {
    font-family: "Crimson Pro", serif;
    font-weight: 500;
    line-height: 0.92;
    color: var(--ink-white);
  }
  .card--front .card__content { padding-top: 62px; }
  .card--front .brand__square { width: 88px; height: 88px; margin-right: 16px; }
  .card--front .brand__name { font-size: 46px; }
  .front__url {
    margin-top: 20px;
    font-size: 20px;
    font-weight: 700;
  }
  .card--back .card__content { padding-top: 34px; }
  .card--back .brand__square { width: 58px; height: 58px; margin-right: 10px; border-radius: 6px; }
  .card--back .brand__name { font-size: 30px; }
  .person__name {
    margin-top: 18px;
    font-size: 31px;
    font-weight: 700;
    line-height: 1;
  }
  .person__quals {
    margin-top: 4px;
    font-size: 16px;
    font-weight: 300;
    color: var(--ink-soft);
  }
  .contact {
    margin-top: 18px;
    text-align: center;
    font-size: 15px;
    font-weight: 400;
    line-height: 1.3;
  }
  .contact__label { font-weight: 700; }
</style>
</head>
<body>
<main class="stage">
  <section class="card card--front">
    <div class="card__pattern" role="img" aria-label="Dark teal damask floral pattern background"></div>
    <div class="card__content">
      <div class="brand">
        <span class="brand__square"></span>
        <span class="brand__name">Lantern<br>Education</span>
      </div>
      <p class="front__url">www.lanterneducation.com</p>
    </div>
  </section>

  <section class="card card--back">
    <div class="card__pattern" role="img" aria-label="Dark teal damask floral pattern background"></div>
    <div class="card__content">
      <div class="brand">
        <span class="brand__square"></span>
        <span class="brand__name">Lantern<br>Education</span>
      </div>
      <h1 class="person__name">Name Surname</h1>
      <p class="person__quals">Educational qualifications</p>
      <div class="contact">
        <p><span class="contact__label">Mobile:</span> 555.014.2277</p>
        <p><span class="contact__label">Email:</span> name@lanterneducation.com</p>
        <p><span class="contact__label">Website:</span> www.lanterneducation.com</p>
      </div>
    </div>
  </section>
</main>
</body>
</html>
```